Local fast-growing company in the service sector

We are looking for a modern business card design, which should also appear on our letterheads

Target Market(s)

Private and industrial sectors

Contact Information for Business Card

Vorname Name
Kellberger Str. 18
73614 Lindenau
Tel.: 07146-839214-0
Name@agentur-kvtl.de

Colors
9d9d9d
919191
aaaaaa

Requirements
Must have
• The logo (file) in silver

```html
<!DOCTYPE html>
<html lang="de">
<head>
<meta charset="utf-8">
<title>KVTL Visitenkarte</title>
<link rel="stylesheet" href="https://fonts.googleapis.com/css2?family=Comfortaa:wght@500&family=Michroma&family=Orbitron:wght@700&display=swap">
<style>
  :root {
    --page-bg: #e8e5e1;
    --card-top: #444446;
    --card-bottom: #2f2f31;
    --silver: #aaaaaa;
    --silver-light: #c4c4c4;
    --silver-mid: #9d9d9d;
    --address: #b39e93;
  }
  html, body {
    margin: 0;
    width: 1200px;
    height: 1010px;
    overflow: hidden;
    background: var(--page-bg);
  }
  .canvas {
    position: relative;
    width: 1200px;
    height: 1010px;
  }
  .business-card {
    position: absolute;
    left: 100px;
    top: 215px;
    width: 1000px;
    height: 580px;
    background: linear-gradient(160deg, var(--card-top), var(--card-bottom));
    box-shadow: 0 10px 30px rgba(0,0,0,0.18);
    font-family: "Comfortaa", sans-serif;
  }
  .holder-name {
    position: absolute;
    left: 48px;
    top: 80px;
    margin: 0;
    font-family: "Orbitron", sans-serif;
    font-weight: 700;
    font-size: 26px;
    line-height: 34px;
    letter-spacing: 3px;
    color: var(--silver-light);
  }
  .brand {
    position: absolute;
    left: 641px;
    top: 226px;
    width: 304px;
    text-align: center;
    font-family: "Michroma", sans-serif;
    font-weight: 400;
    color: var(--silver-light);
  }
  .brand-name {
    display: block;
    font-size: 66px;
    line-height: 1;
    letter-spacing: 6px;
  }
  .brand-domain {
    display: block;
    margin-top: 12px;
    font-size: 25px;
    line-height: 1;
    letter-spacing: 1px;
  }
  .contact-list {
    position: absolute;
    left: 46px;
    top: 392px;
    margin: 0;
    padding: 0;
    list-style: none;
  }
  .contact-item {
    display: flex;
    align-items: center;
    height: 33px;
    font-size: 23px;
    font-weight: 500;
    letter-spacing: 1px;
    color: var(--silver-light);
  }
  .contact-icon {
    width: 18px;
    height: 18px;
    margin: 0 24px 0 4px;
    fill: var(--silver);
  }
  .address {
    position: absolute;
    left: 46px;
    top: 500px;
    margin: 0;
    font-size: 23px;
    font-weight: 500;
    letter-spacing: 1px;
    color: var(--address);
  }
</style>
</head>
<body>
<div class="canvas">
  <article class="business-card">
    <h1 class="holder-name">VORNAME NAME</h1>

    <div class="brand">
      <span class="brand-name">KVTL</span>
      <span class="brand-domain">agentur-kvtl.de</span>
    </div>

    <ul class="contact-list">
      <li class="contact-item">
        <svg class="contact-icon" viewBox="0 0 20 20" aria-hidden="true">
          <path d="M2 6c0-2 2-3 8-3s8 1 8 3v2h-4V6.5H6V8H2z"/>
          <path d="M5 9h10l2 8H3z"/>
        </svg>
        07146-839214-0
      </li>
      <li class="contact-item">
        <svg class="contact-icon" viewBox="0 0 20 20" aria-hidden="true">
          <path d="M1 4h18v12H1z M3 6l7 5 7-5" fill="none" stroke="var(--silver)" stroke-width="2"/>
        </svg>
        Name@agentur-kvtl.de
      </li>
      <li class="contact-item">
        <svg class="contact-icon" viewBox="0 0 20 20" aria-hidden="true">
          <circle cx="10" cy="10" r="8" fill="none" stroke="var(--silver)" stroke-width="1.6"/>
          <ellipse cx="10" cy="10" rx="3.5" ry="8" fill="none" stroke="var(--silver)" stroke-width="1.4"/>
          <path d="M2 10h16" stroke="var(--silver)" stroke-width="1.4"/>
        </svg>
        www.agentur-kvtl.de
      </li>
    </ul>

    <p class="address">Kellberger Str. 18 73614 Lindenau</p>
  </article>
</div>
</body>
</html>
```